Design a calming beauty medical salon & spa website based in Hong Kong

We need help building an informational website for a beauty salon in Hong Kong. The local salon provides facials, massages, body and other slimming treatments in a relaxing environment. We offer some non-invasive medical treatments, such as botox. Having built the business on word of mouth, it is now time for us to launch a website to help market the business better. Website requirements:

-Must be responsive
-Use vibrant but clean colours. not too many, 1-2 colours
-Must be bilingual (switch between Chinese traditional and English)
-Our current website is host on a server, not using any particular platforms like wordpress

Pages:
1/ Homepage
2/ About us (incorporate gallery of salon photos and history of company)
3/ Promotions and latest deals (and leads them to sign up for more info, maybe pop-up small window when you click on a promotion)
4/ Treatment menus
4.1/Body treatments
4.2/ Face treatments
4.3/ Slimming treatments
5/ Showcasing products sold (no e-commerce functionality, just showing off products)
6/ Contact us (tel, address, map, opening hrs)

Footer - must haves include contact us info, privacy policy, terms & conditions, copyright blurb, join our company/employment page (with a form)

For information (comparable websites we like):
http://veltora.com/
http://pambrix.com.hk/tc/aboutpambrix/background.php#centerenvi
Attaching a very first draft concept for this website
Attaching pictures of the beauty salon
Attaching logo

Target Market(s)

Hong Kong based, Chinese, females, 30-50+ age. 90% female clients.

Industry/Entity Type

Beauty Salon

Number of Pages Required

5+ page

Font styles to use
Sans Serif

Colors
f9d9e8
fbd3d4
fee3d5
fbe7d2
fee18a
fbf289
ffffff

Requirements
Must have
• interactive elements on website, such as scrolling banner photo headers
• incorporate photos of website salon
• connect to facebook page

```html
<!DOCTYPE html>
<html lang="en">
<head>
<meta charset="utf-8">
<title>Lumera Beauty – Body Treatment</title>
<link rel="stylesheet" href="https://fonts.googleapis.com/css2?family=Montserrat:wght@400;500;600&family=PT+Sans:wght@400;700&family=Roboto+Condensed:wght@700&display=swap">
<style>
:root{
  --purple:#6a1276;
  --purple-deep:#640e6e;
  --yellow:#fbf289;
  --ink:#111;
  --text:#3a3a3a;
  --white:#fff;
}
*{box-sizing:border-box;margin:0;padding:0}
html,body{width:1200px;height:1040px;overflow:hidden;background:var(--white)}
body{position:relative;font-family:"PT Sans",sans-serif;color:var(--text)}
.abs{position:absolute}

.topbar{left:439px;top:0;width:761px;height:35px;background:var(--purple);border-bottom-left-radius:22px;box-shadow:-5px 2px 0 var(--yellow);display:flex;align-items:center;justify-content:flex-end;padding-right:86px;font-family:"Montserrat",sans-serif;font-weight:500;font-size:14px;color:var(--white);letter-spacing:.5px}
.topbar span{display:flex;align-items:center;gap:8px}
.topbar .sep{width:1px;height:16px;background:rgba(255,255,255,.35);margin:0 34px}

.brand{left:86px;top:30px;display:flex;align-items:center;gap:10px;font-family:"Montserrat",sans-serif;font-weight:600;font-size:30px;color:var(--purple)}
.brand i{width:52px;height:52px;border-radius:50%;background:var(--purple);display:block}

.info{top:62px;display:flex;align-items:center;gap:16px;font-family:"Montserrat",sans-serif;font-size:14.5px;letter-spacing:1px;line-height:21px;color:var(--ink)}
.info.phone{left:477px}
.info.hours{left:752px}

.mainnav{left:0;top:126px;width:1200px;height:35px;background:var(--purple);display:flex;justify-content:space-between;align-items:center;padding:0 86px;font-family:"Montserrat",sans-serif;font-size:16px;letter-spacing:2px;color:var(--white)}

.page-title{left:86px;top:214px;font-family:"Roboto Condensed",sans-serif;font-weight:700;font-size:33px;letter-spacing:2px;color:var(--ink)}
.photo{left:86px;top:273px;width:500px;height:328px;border:1px solid #e2dede;background:linear-gradient(135deg,#f3eeec 0%,#f0d5c4 45%,#e5b79c 75%,#f4efec 100%)}

.copy{font-size:13.5px;line-height:21px;letter-spacing:.6px}
.copy-side{left:613px;top:294px;width:497px}
.copy-side ul{list-style:none;margin:7px 0 5px}
.copy-side li{line-height:26.3px;padding-left:13px;position:relative}
.copy-side li::before{content:"";position:absolute;left:0;top:10px;width:5px;height:5px;border-top:1.5px solid var(--purple);border-right:1.5px solid var(--purple);transform:rotate(45deg)}
.copy-wide{left:86px;top:623px;width:1030px}

.footer{left:0;top:741px;width:1200px;height:299px;background:var(--purple-deep);color:var(--white)}
.footer .brand{color:var(--white);top:45px;left:86px}
.footer .brand i{background:var(--white)}
.footer-blurb{left:87px;top:141px;width:330px;font-size:13.5px;line-height:21px;letter-spacing:.6px}
.footer-social{left:87px;top:200px;display:flex;align-items:center;gap:9px;font-size:13.5px;letter-spacing:1.2px}
.footer-social i{width:31px;height:31px;border-radius:50%;background:#3d4f8e;display:block}
.copyright{left:87px;top:241px;font-size:13.5px;letter-spacing:.6px}
.footer h3{font-family:"PT Sans",sans-serif;font-weight:400;font-size:22px;letter-spacing:2px}
.quick{left:517px;top:34px}
.quick ul{list-style:none;margin-top:10px}
.quick li{font-size:13.5px;line-height:21px;letter-spacing:.8px}
.contact{left:803px;top:34px;width:320px}
.contact h4{font-weight:700;font-size:13.5px;letter-spacing:1.2px;margin-top:10px}
.contact p{font-size:13.5px;line-height:21px;letter-spacing:.6px;margin-top:4px}
</style>
</head>
<body>

<div class="abs topbar">
  <span><svg width="16" height="12" viewBox="0 0 16 12"><rect width="16" height="12" rx="1" fill="#fff"/><path d="M0 1l8 6 8-6" stroke="#6a1276" stroke-width="1.6" fill="none"/></svg>hello@lumerabeauty.hk</span>
  <i class="sep"></i>
  <span>Connect with us</span>
  <i class="sep"></i>
  <span>ENG&nbsp; I &nbsp;CN</span>
</div>

<div class="abs brand"><i></i>Lumera Beauty</div>

<div class="abs info phone">
  <svg width="34" height="34" viewBox="0 0 34 34"><path d="M8 4l5 6-3 3c2 5 6 9 11 11l3-3 6 5-4 4C15 32 2 19 4 8z" fill="#6a1276"/><path d="M20 6a9 9 0 0 1 8 8M20 1a14 14 0 0 1 13 13" stroke="#6a1276" stroke-width="2" fill="none"/></svg>
  <div>TEL: 23456789<br>WHATSAPP: 5123 4567</div>
</div>
<div class="abs info hours">
  <svg width="34" height="34" viewBox="0 0 34 34"><rect x="1" y="4" width="26" height="24" rx="2" fill="none" stroke="#6a1276" stroke-width="2.4"/><rect x="1" y="4" width="26" height="6" fill="#6a1276"/><path d="M7 1v6M21 1v6" stroke="#6a1276" stroke-width="2.4"/><circle cx="26" cy="25" r="7.5" fill="#fff" stroke="#6a1276" stroke-width="2.4"/><path d="M26 21v4h3" stroke="#6a1276" stroke-width="2" fill="none"/><g fill="#6a1276"><rect x="5" y="13" width="3" height="3"/><rect x="10" y="13" width="3" height="3"/><rect x="15" y="13" width="3" height="3"/><rect x="5" y="18" width="3" height="3"/><rect x="10" y="18" width="3" height="3"/></g></svg>
  <div>MON TO FRI: 10.30 AM TO 9.30PM<br>SAT AND HOLIDAY: 10.30 AM TO 7.30PM</div>
</div>

<nav class="abs mainnav">
  <span>HOME</span><span>ABOUT US</span><span>PROMOTIONS AND LATEST DEALS</span><span>TREATMENT</span><span>PRODUCTS</span><span>CONTACT US</span>
</nav>

<h1 class="abs page-title">BODY TREATMENT</h1>
<div class="abs photo" role="img" aria-label="Photo of a client receiving cupping therapy on her back"></div>

<div class="abs copy copy-side">
  <p>Lorem Ipsum is simply dummy text of the printing and typesetting industry. Lorem Ipsum has been the industry's standard dummy text ever since the 1500s, when an unknown printer took a galley of type and scrambled it to make a type specimen book.</p>
  <ul>
    <li>Lorem Ipsum is simply dummy text of the printing and typesetting.</li>
    <li>Lorem Ipsum is simply dummy text</li>
    <li>Lorem Ipsum is simply dummy text of the printing</li>
    <li>Lorem Ipsum is simply dummy text &nbsp;and typesetting.</li>
  </ul>
  <p>Lorem Ipsum is simply dummy text of the printing and typesetting industry. Lorem Ipsum has been the industry's standard dummy text ever since the 1500s, when an unknown printer took a galley of type and scrambled it to make a type specimen book.</p>
</div>

<p class="abs copy copy-wide">Lorem Ipsum is simply dummy text of the printing and typesetting industry. Lorem Ipsum has been the industry's standard dummy text ever since the 1500s, when an unknown printer took a galley of type and scrambled it to make a type specimen book. It has survived not only five centuries, but also the leap into electronic typesetting, remaining essentially unchanged. It was popularised in the 1960s with the release of Letraset sheets containing Lorem Ipsum passages, and more recently with desktop publishing software like Aldus PageMaker including versions of Lorem Ipsum.</p>

<footer class="abs footer">
  <div class="abs brand"><i></i>Lumera Beauty</div>
  <p class="abs footer-blurb">It is a long established fact that a reader will be distracted by the readable content.</p>
  <div class="abs footer-social"><i></i>Connect with us</div>
  <p class="abs copyright">Copyright © 2017 &nbsp;I &nbsp;All Rights Reserved.</p>

  <div class="abs quick">
    <h3>QUICK LINKS</h3>
    <ul>
      <li>Home</li><li>About Us</li><li>Promotions and Latest Deals</li><li>Treatment</li><li>Products</li><li>Contact Us</li><li>Privacy Policy</li><li>Terms &amp; Conditions</li><li>Join Us</li>
    </ul>
  </div>

  <div class="abs contact">
    <h3>CONTACT INFO</h3>
    <h4>ADDRESS</h4>
    <p>12/F., Silver Lotus Centre, 22-24 Harbour Lane, Tsim Sha Tsui, Kowloon, Hong Kong</p>
    <h4>PHONE</h4>
    <p>2345 6789 &nbsp;/ &nbsp;5123 4567</p>
    <h4>EMAIL</h4>
    <p>hello@lumerabeauty.hk</p>
  </div>
</footer>

</body>
</html>
```